Poster for mountain bike and trail run competition

I am looking for a poster design for a charitable mountain bike and trail run race. It should be something fun, colorful, which can attract participants. The area in which the competition takes place is dominated by hills and by the Nera river which has a beautiful gorge.. I am attaching some of our previous (poorly designed) posters. The poster should have a place where I can add the sponsor logos, which I will do by myself, in the following months.
Text:
Headline: "Vadul Tomirei Mountain Bike and Trail Run Race"
small headline: "Editia a-6a"
small headline: "Sasca Romana, 10-11 IUNIE 2023"
other text:
"10 IUNIE - Concurs Mountain Bike & Concert
11 IUNIE - Concurs Trail Run"
text for enrollments: "inscrieri pe www.ulmetcross.ro"

Thanks

• a space where I can add sponsor logos, editable file to be provided (AI, photoshop or corel)

```html
<!DOCTYPE html>
<html lang="ro">
<head>
<meta charset="utf-8">
<title>Vadul Tomirei Mountain Bike and Trail Run Race</title>
<link href="https://fonts.googleapis.com/css2?family=Graduate&family=Russo+One&family=Teko:wght@400;500&family=Roboto+Condensed:wght@700&family=Montserrat:wght@400;600;800&display=swap" rel="stylesheet">
<style>
  :root{
    --page:#f7f7f7;
    --night:#000;
    --deep-blue:#0b128a;
    --blue:#1624c4;
    --cyan:#19d4f5;
    --neon-cyan:#3fe3ff;
    --neon-pink:#ff6fe8;
    --pink-fill:#ffd4fb;
    --white:#ffffff;
    --sponsor-ink:#4a4f63;
  }
  *{margin:0;padding:0;box-sizing:border-box}
  html,body{width:857px;height:1200px;overflow:hidden;background:var(--page)}
  .canvas{position:relative;width:857px;height:1200px;background:var(--page)}
  .poster{position:absolute;left:78px;top:105px;width:701px;height:990px;overflow:hidden;
    background:linear-gradient(180deg,var(--night) 0,var(--night) 470px,#0a1070 560px,var(--blue) 650px,#0d1699 760px,#070c5c 840px,var(--deep-blue) 849px)}
  .scene{position:absolute;left:0;top:0;width:701px;height:330px;
    background:linear-gradient(180deg,#e38a4f 0%,#c9655c 25%,#8d4550 45%,#e5a06a 70%,#f2b77c 82%,#1a0c10 100%)}
  .scene-side{position:absolute;top:170px;width:70px;height:110px;background:linear-gradient(180deg,#18c8ee,#0b6f8a)}
  .scene-side.left{left:0}
  .scene-side.right{right:0}
  .artwork{position:absolute;left:0;top:0;width:701px;height:990px}
  .title-neon{font-family:"Graduate",serif;fill:none;stroke:var(--neon-cyan);stroke-width:2.2;filter:drop-shadow(0 0 4px var(--neon-cyan)) drop-shadow(0 0 8px #1aa8ff)}
  .title-pink{font-family:"Russo One",sans-serif;fill:var(--pink-fill);stroke:var(--neon-pink);stroke-width:1.2;filter:drop-shadow(0 0 5px var(--neon-pink))}
  .edition-text{font-family:"Teko",sans-serif;font-weight:500;fill:var(--white)}
  .place-text{font-family:"Teko",sans-serif;font-weight:500;fill:var(--cyan)}
  .shield-text{font-family:"Roboto Condensed",sans-serif;font-weight:700;fill:var(--white)}
  .date-text{font-family:"Montserrat",sans-serif;font-weight:800;fill:var(--cyan)}
  .signup{position:absolute;left:0;width:701px;top:812px;text-align:center;
    font-family:"Montserrat",sans-serif;font-size:16.5px;color:var(--cyan);letter-spacing:.3px}
  .sponsors{position:absolute;left:0;top:849px;width:701px;height:141px;background:var(--white);
    display:grid;grid-template-columns:repeat(6,1fr);grid-auto-rows:1fr;align-items:center;justify-items:center;padding:10px 30px}
  .sponsor{font-family:"Montserrat",sans-serif;font-weight:600;font-size:10.5px;color:var(--sponsor-ink);white-space:nowrap}
  .sponsor.accent{color:#c0392b}
  .sponsor.blue{color:#1f5fa8}
</style>
</head>
<body>
<div class="canvas">
  <section class="poster">
    <div class="scene" role="img" aria-label="Illustration: sunset mountains, lake and pine forest with silhouettes of cyclists and trail runners">
      <div class="scene-side left"></div>
      <div class="scene-side right"></div>
    </div>

    <svg class="artwork" viewBox="0 0 701 990" width="701" height="990">
      <defs>
        <linearGradient id="shieldFill" x1="0" y1="0" x2="0" y2="1">
          <stop offset="0" stop-color="#1430c8"/>
          <stop offset="1" stop-color="#050a40"/>
        </linearGradient>
      </defs>

      <text class="title-neon" x="83" y="410" font-size="84" textLength="530" lengthAdjust="spacingAndGlyphs">VADUL TOMIREI</text>
      <text class="title-pink" x="87" y="491" font-size="74" textLength="521" lengthAdjust="spacingAndGlyphs">MOUNTAIN BIKE</text>
      <text class="title-pink" x="83" y="552" font-size="54" textLength="531" lengthAdjust="spacingAndGlyphs">AND TRAIL RUN RACE</text>

      <rect x="84" y="569" width="245" height="45" rx="4" fill="var(--deep-blue)" stroke="var(--white)" stroke-width="2.5"/>
      <text class="edition-text" x="206" y="609" font-size="46" text-anchor="middle" textLength="220" lengthAdjust="spacingAndGlyphs">EDITIA A-6A</text>
      <text class="place-text" x="344" y="609" font-size="46" textLength="272" lengthAdjust="spacingAndGlyphs">SASCA ROMANA</text>

      <g class="shield">
        <path d="M120 631 H292 V651 L277 660 V755 L206 792 L135 755 V660 L120 651 Z" fill="url(#shieldFill)" stroke="var(--cyan)" stroke-width="2"/>
        <path d="M120 631 H292 V651 L277 660 H135 L120 651 Z" fill="var(--cyan)"/>
        <text class="shield-text" x="206" y="683" font-size="22" text-anchor="middle">10 IUNIE</text>
        <text class="shield-text" x="206" y="713" font-size="22" text-anchor="middle">CONCURS</text>
        <text class="shield-text" x="206" y="742" font-size="22" text-anchor="middle">MOUNTAIN</text>
        <text class="shield-text" x="206" y="764" font-size="14.5" text-anchor="middle">BIKE &amp; CONCERT</text>
      </g>
      <g class="shield">
        <path d="M405 631 H577 V651 L562 660 V755 L491 792 L420 755 V660 L405 651 Z" fill="url(#shieldFill)" stroke="var(--cyan)" stroke-width="2"/>
        <path d="M405 631 H577 V651 L562 660 H420 L405 651 Z" fill="var(--cyan)"/>
        <text class="shield-text" x="491" y="684" font-size="22" text-anchor="middle">11 IUNIE</text>
        <text class="shield-text" x="491" y="714" font-size="22" text-anchor="middle">CONCURS</text>
        <text class="shield-text" x="491" y="743" font-size="22" text-anchor="middle">TRAIL RUN</text>
      </g>

      <text class="date-text" x="350" y="687" font-size="27" text-anchor="middle">10-11</text>
      <text class="date-text" x="350" y="720" font-size="27" text-anchor="middle">IUNIE</text>
      <text class="date-text" x="350" y="753" font-size="27" text-anchor="middle">2023</text>
    </svg>

    <p class="signup">inscrieri pe @ www.ulmetcross.ro</p>

    <div class="sponsors" aria-label="Sponsori">
      <span class="sponsor accent">Brumar Radler</span>
      <span class="sponsor">Pedalo Shop</span>
      <span class="sponsor blue">Printava</span>
      <span class="sponsor blue">Geomarc</span>
      <span class="sponsor">Aerolis</span>
      <span class="sponsor blue">Radio Banat Sud</span>
      <span class="sponsor">Fauna Vie</span>
      <span class="sponsor">Lumivia</span>
      <span class="sponsor blue">Axomet</span>
      <span class="sponsor">Punct Final</span>
      <span class="sponsor">Hidrofit</span>
      <span class="sponsor">Mediaport</span>
      <span class="sponsor accent">Crestline</span>
      <span class="sponsor">Club Civic Cetate</span>
      <span class="sponsor accent">Vertisport</span>
      <span class="sponsor accent">Electra</span>
      <span class="sponsor">Fitlab</span>
      <span class="sponsor">Print Atelier</span>
      <span class="sponsor accent">Fermora</span>
      <span class="sponsor blue">Netrix</span>
      <span class="sponsor blue">Stepwise</span>
      <span class="sponsor accent">Casa Lacului</span>
      <span class="sponsor blue">Gazotec</span>
      <span class="sponsor">Consultia</span>
      <span class="sponsor">Forma Design</span>
      <span class="sponsor">Cetatea Park</span>
      <span class="sponsor blue">Agenda Oraș</span>
    </div>
  </section>
</div>
</body>
</html>
```